Web Developer Needs a Business Card Design

I need a personal business card design that represents me as a web developer for potential employers. I would like the background to be a dark color on the front for contrast with my logo and name. The back will have all my information along with a smaller version of the logo. I want something with a modern look and feel, not too conservative. This will be used for potential employers and freelance work.

Industry/Entity Type

Business

Contact Information for Business Card

Front should have my logo and name. The back should have all my personal information which would include: name: Tom Varulek, phone: 570-614-3098, email: tomvarulek@quillbox.net, website url: www.tomvarulek.net, logo, web developer.

Font styles to use
Sans Serif

Requirements
Must have
• Must include my logo. The color palette base color will be the logo color.

```html
<!DOCTYPE html>
<html lang="en">
<head>
<meta charset="utf-8">
<title>Tom Varulek — Business Card</title>
<link rel="stylesheet" href="https://fonts.googleapis.com/css2?family=Fira+Sans:wght@400;500&display=swap">
<style>
  :root {
    --mint: #8fd3c7;
    --mint-light: #c4ebe4;
    --mint-deep: #6fc1b3;
    --ink: #0b0b0c;
    --white: #ffffff;
    --stage: #e9ecec;
  }
  * { margin: 0; padding: 0; box-sizing: border-box; }
  html, body { width: 1200px; height: 892px; overflow: hidden; }
  body {
    background: var(--stage);
    font-family: "Fira Sans", sans-serif;
    display: flex;
    flex-direction: column;
    align-items: center;
    justify-content: center;
    gap: 48px;
  }
  .card {
    position: relative;
    width: 630px;
    height: 360px;
    overflow: hidden;
    box-shadow: 0 10px 30px rgba(0,0,0,.18);
  }
  /* Info side */
  .card--info { background: var(--ink); }
  .card--info .panel { position: absolute; inset: 0; }
  .tab { position: absolute; right: 0; width: 26px; background: var(--mint); }
  .tab--top { top: 0; height: 34px; }
  .tab--mid { top: 150px; height: 60px; }
  .identity { position: absolute; top: 48px; right: 150px; text-align: right; }
  .identity .name {
    color: var(--mint);
    font-size: 38px; font-weight: 500; letter-spacing: .5px;
  }
  .identity .role {
    color: var(--white);
    font-size: 21px; font-weight: 400; margin-top: 2px;
  }
  .contacts {
    position: absolute; top: 176px; right: 50px;
    list-style: none;
  }
  .contacts li {
    display: flex; align-items: center; justify-content: flex-end;
    gap: 46px;
    color: var(--white);
    font-size: 21px; line-height: 38px;
  }
  .contacts svg { width: 18px; height: 18px; flex: none; }
  /* Logo side */
  .card--logo {
    background: radial-gradient(ellipse at 35% 30%, var(--mint-light) 0%, var(--mint) 55%, var(--mint-deep) 100%);
    display: flex; flex-direction: column; align-items: center; justify-content: center;
    gap: 22px;
  }
  .mark {
    width: 150px; height: 150px; border-radius: 50%;
    border: 10px solid var(--white);
  }
  .card--logo .name {
    color: var(--white); font-size: 40px; font-weight: 500; letter-spacing: .5px;
  }
</style>
</head>
<body>

<section class="card card--info" aria-label="Card back with contact details">
  <svg class="panel" viewBox="0 0 630 360" aria-hidden="true">
    <path d="M0 0 H150 Q250 180 150 360 H0 Z" fill="var(--mint)"/>
    <path d="M0 0 H150 Q250 180 150 360 H0 Z" fill="url(#fade)"/>
    <path d="M168 0 Q268 180 168 360" fill="none" stroke="var(--white)" stroke-width="7"/>
    <circle cx="200" cy="180" r="62" fill="var(--white)"/>
    <circle cx="200" cy="180" r="44" fill="var(--mint)"/>
    <defs>
      <linearGradient id="fade" x1="0" y1="0" x2="1" y2="0">
        <stop offset="0" stop-color="#ffffff" stop-opacity=".35"/>
        <stop offset="1" stop-color="#ffffff" stop-opacity="0"/>
      </linearGradient>
    </defs>
  </svg>
  <div class="tab tab--top"></div>
  <div class="tab tab--mid"></div>

  <div class="identity">
    <div class="name">Tom Varulek</div>
    <div class="role">web developer</div>
  </div>

  <ul class="contacts">
    <li>570-614-3098
      <svg viewBox="0 0 18 18" aria-hidden="true"><rect width="18" height="18" fill="var(--white)"/><path d="M5 4 L7 4 L8 7 L6.8 8 Q8 10.5 10 11.2 L11 10 L14 11 L14 13 Q9 14 5 9 Q4 6 5 4Z" fill="var(--ink)"/></svg>
    </li>
    <li>www.tomvarulek.net
      <svg viewBox="0 0 18 18" aria-hidden="true"><rect width="18" height="18" fill="var(--white)"/><circle cx="9" cy="9" r="5" fill="none" stroke="var(--ink)" stroke-width="1.4"/><path d="M4 9 H14 M9 4 Q6 9 9 14 Q12 9 9 4" fill="none" stroke="var(--ink)" stroke-width="1.1"/></svg>
    </li>
    <li>tomvarulek@quillbox.net
      <svg viewBox="0 0 18 18" aria-hidden="true"><rect width="18" height="18" fill="var(--white)"/><rect x="3.5" y="5" width="11" height="8" fill="none" stroke="var(--ink)" stroke-width="1.3"/><path d="M3.5 5 L9 10 L14.5 5" fill="none" stroke="var(--ink)" stroke-width="1.3"/></svg>
    </li>
  </ul>
</section>

<section class="card card--logo" aria-label="Card front with name">
  <div class="mark" aria-hidden="true"></div>
  <div class="name">Tom Varulek</div>
</section>

</body>
</html>
```